Machinery Harbor Corp - Business Card Design

Need a new modern designed business card that is different and stands out to represent my equipment financing company. Machinery Harbor Corp finances all types of equipment and all types of industries. We like to do equipment financing a different way by putting customers first and want our card to represent that different approach to business. I want a card that some remembers when they receive it so it sticks in their mind and makes that wow impression.

Card should have a black background so the logo stands out. It can be horizontial or vertical or a combination of both.

Front of card information is below that shows the information that would go on my card. That is where I want a different look or design to stand out. The front could be split black/orange colour so the logo could pop on black side and information on orange side with different lettering. Just outside the box thinking on the front of the card. Open to any type of design.

Back of card is below which i I like unless you have a different spin to provide or a different idea that would make the card better as I am open to anything that looks great.

Target Market(s)

Machinery Harbor Corp deals with business owners in all industries.

Industry/Entity Type

Business

Contact Information for Business Card

Colors

Designer to choose colors to be used in the design.

Requirements
Must have
• Modern
• Different
• Stand Out
• Makes an Impression

```html
<!DOCTYPE html>
<html lang="en">
<head>
<meta charset="utf-8">
<title>Machinery Harbor Corp – Business Card</title>
<link href="https://fonts.googleapis.com/css2?family=Cinzel:wght@400&family=Lato:wght@400;700&display=swap" rel="stylesheet">
<style>
  :root {
    --backdrop: #3b3431;
    --card-black: #1c1d1f;
    --strip-white: #f7f6f4;
    --brand-orange: #f0611f;
    --text-white: #f2f2f2;
    --text-soft: #d9d9d9;
  }
  * { box-sizing: border-box; margin: 0; padding: 0; }
  html, body {
    width: 1200px;
    height: 780px;
    overflow: hidden;
    background: var(--backdrop);
  }
  .canvas {
    position: relative;
    width: 1200px;
    height: 780px;
  }
  .card {
    position: absolute;
    top: 247px;
    width: 500px;
    height: 286px;
    background: var(--card-black);
    box-shadow: 0 14px 30px rgba(0,0,0,0.45);
    overflow: hidden;
  }
  .card--back { left: 70px; }
  .card--front { left: 630px; }

  /* Back card */
  .back-brand {
    position: absolute;
    right: 60px;
    top: 50%;
    transform: translateY(-50%);
    display: flex;
    align-items: center;
    gap: 12px;
  }
  .brand-square {
    width: 16px;
    height: 16px;
    background: var(--brand-orange);
  }
  .brand-name {
    font-family: "Cinzel", serif;
    font-weight: 400;
    color: var(--brand-orange);
    letter-spacing: 0.08em;
    line-height: 1.2;
  }
  .back-brand .brand-name { font-size: 19px; }

  /* Front card */
  .side-strip {
    position: absolute;
    left: 0;
    top: 0;
    width: 104px;
    height: 100%;
    background: var(--strip-white);
    display: flex;
    align-items: center;
    justify-content: center;
  }
  .side-strip .brand-name {
    writing-mode: vertical-rl;
    transform: rotate(180deg);
    font-size: 22px;
    text-align: center;
    white-space: nowrap;
  }
  .holder {
    position: absolute;
    left: 142px;
    top: 100px;
    font-family: "Lato", sans-serif;
  }
  .holder-name {
    font-weight: 700;
    font-size: 19px;
    color: var(--text-white);
    letter-spacing: 0.02em;
  }
  .holder-title {
    font-weight: 400;
    font-size: 13px;
    color: var(--text-soft);
    letter-spacing: 0.04em;
    margin-top: 2px;
  }
  .contact {
    position: absolute;
    left: 142px;
    top: 178px;
    list-style: none;
    font-family: "Lato", sans-serif;
    font-size: 13px;
    line-height: 1.6;
    color: var(--text-white);
  }
  .front-brand {
    position: absolute;
    right: 34px;
    top: 118px;
    display: flex;
    align-items: center;
    gap: 10px;
  }
  .front-brand .brand-name {
    font-size: 13px;
    width: 110px;
  }
</style>
</head>
<body>
<main class="canvas">
  <section class="card card--back" aria-label="Card back">
    <div class="back-brand">
      <span class="brand-square"></span>
      <span class="brand-name">Machinery<br>Harbor Corp</span>
    </div>
  </section>

  <section class="card card--front" aria-label="Card front">
    <div class="side-strip">
      <span class="brand-name">Machinery Harbor<br>Corp</span>
    </div>
    <div class="holder">
      <p class="holder-name">DEAN MARLOW</p>
      <p class="holder-title">PRESIDENT</p>
    </div>
    <ul class="contact">
      <li>555.010.2291</li>
      <li>dean@machineryharborcorp.ca</li>
      <li>www.machineryharborcorp.ca</li>
    </ul>
    <div class="front-brand">
      <span class="brand-square"></span>
      <span class="brand-name">Machinery Harbor Corp</span>
    </div>
  </section>
</main>
</body>
</html>
```